Voranta Imports Busisness cards and logo

Voranta imports is a brand new wholesale company located in Londonderry, New Hampshire dedicated to finding unique products from around the world.
Licensed to sell wine and spirits in the state and also authorized distributors of Pale Meadow Design, a manufacturer of girls and women shoes. Other products that we are currently trying to import are cheese and frozen food from Spain.
We would like a design that portraits our diversity of products and wholesale capabilities

```html
<!DOCTYPE html>
<html lang="en">
<head>
<meta charset="utf-8">
<title>Voranta Imports – Business Card</title>
<link rel="stylesheet" href="https://fonts.googleapis.com/css2?family=Open+Sans:ital,wght@0,400;0,600;0,700;1,400;1,700&display=swap">
<style>
  :root{
    --page:#e6e6e6;
    --card-white:#ffffff;
    --card-grey:#e4e4e4;
    --ink:#4a4a4a;
    --ink-soft:#5a5a5a;
    --brand-grey:#5b5b5b;
    --green-dark:#3c7533;
    --green-mid:#5c9a3e;
    --green-light:#86bf4c;
    --swoosh-grey:#9c9c9c;
    --white:#ffffff;
  }
  *{box-sizing:border-box;margin:0;padding:0}
  html,body{width:1200px;height:900px;overflow:hidden;background:var(--page)}
  body{font-family:"Open Sans",Arial,sans-serif;position:relative}

  .card{
    position:absolute;left:280px;width:640px;height:366px;
    border-radius:24px;overflow:hidden;
    box-shadow:0 6px 18px rgba(0,0,0,.18);
    background:radial-gradient(ellipse at 40% 35%,var(--card-white) 0%,var(--card-grey) 100%);
  }
  .card--back{top:40px}
  .card--front{top:494px}

  .card__art{position:absolute;inset:0;width:100%;height:100%}

  .brand{position:absolute;display:flex;align-items:center;gap:12px}
  .brand__dot{width:50px;height:50px;border-radius:50%;background:var(--green-mid)}
  .brand__name{font-weight:700;font-size:32px;color:var(--brand-grey);letter-spacing:-.5px;white-space:nowrap}

  .card--back .brand{left:50%;top:50%;transform:translate(-50%,-50%)}
  .card--front .brand{left:26px;top:70px}

  .person{position:absolute;left:56px;top:162px;color:var(--ink)}
  .person__name{font-size:23px;font-weight:700;font-style:italic;line-height:1.2}
  .person__role{font-size:19px;font-style:italic;color:var(--ink-soft);line-height:1.2}

  .contact{position:absolute;left:440px;top:240px;list-style:none;color:var(--white);font-size:12px;line-height:16px;white-space:nowrap}
  .contact li{display:flex;align-items:flex-start;gap:6px}
  .contact svg{flex:none;width:11px;height:11px;margin-top:2.5px}
  .contact .indent{padding-left:17px;display:block}
</style>
</head>
<body>

<section class="card card--back" aria-label="Card back">
  <div class="brand">
    <span class="brand__dot"></span>
    <span class="brand__name">Voranta Imports</span>
  </div>
</section>

<section class="card card--front" aria-label="Card front">
  <svg class="card__art" viewBox="0 0 640 366" preserveAspectRatio="none" aria-hidden="true">
    <defs>
      <linearGradient id="greenField" x1="0" y1="0" x2="1" y2="0">
        <stop offset="0" stop-color="var(--green-dark)"/>
        <stop offset=".55" stop-color="var(--green-mid)"/>
        <stop offset="1" stop-color="var(--green-light)"/>
      </linearGradient>
      <linearGradient id="greySwoosh" x1="0" y1="0" x2="1" y2="0">
        <stop offset="0" stop-color="#b5b5b5"/>
        <stop offset="1" stop-color="#8a8a8a"/>
      </linearGradient>
    </defs>
    <path d="M0 236 C200 252 400 206 640 132 L640 146 C400 220 200 266 0 250 Z" fill="url(#greySwoosh)"/>
    <path d="M0 262 C220 276 420 222 640 158 L640 170 C420 234 220 288 0 274 Z" fill="var(--green-mid)"/>
    <path d="M0 288 C240 302 440 246 640 184 L640 366 L0 366 Z" fill="url(#greenField)"/>
  </svg>

  <div class="brand">
    <span class="brand__dot"></span>
    <span class="brand__name">Voranta Imports</span>
  </div>

  <div class="person">
    <p class="person__name">Daniel Reyes</p>
    <p class="person__role">Owner / C.E.O</p>
  </div>

  <ul class="contact">
    <li>
      <svg viewBox="0 0 12 12"><circle cx="6" cy="6" r="6" fill="#fff"/><path d="M6 2.5a2.2 2.2 0 0 0-2.2 2.2C3.8 6.6 6 9.5 6 9.5s2.2-2.9 2.2-4.8A2.2 2.2 0 0 0 6 2.5z" fill="var(--green-mid)"/></svg>
      <span>Suite # 118, Ridge Bldg,</span>
    </li>
    <li><span class="indent">NH 03053</span></li>
    <li>
      <svg viewBox="0 0 12 12"><circle cx="6" cy="6" r="6" fill="#fff"/><path d="M4 3h1.4l.6 1.6-.8.6a4 4 0 0 0 1.6 1.6l.6-.8 1.6.6V8a1 1 0 0 1-1 1A5 5 0 0 1 3 4a1 1 0 0 1 1-1z" fill="var(--green-mid)"/></svg>
      <span>603-555-0142</span>
    </li>
    <li>
      <svg viewBox="0 0 12 12"><circle cx="6" cy="6" r="6" fill="#fff"/><rect x="4.2" y="2.5" width="3.6" height="7" rx=".7" fill="var(--green-mid)"/></svg>
      <span>603-555-0187</span>
    </li>
    <li>
      <svg viewBox="0 0 12 12"><circle cx="6" cy="6" r="6" fill="#fff"/><rect x="3" y="5" width="6" height="4" fill="var(--green-mid)"/><rect x="4" y="3" width="4" height="2" fill="var(--green-mid)"/></svg>
      <span>603-555-0199</span>
    </li>
    <li>
      <svg viewBox="0 0 12 12"><circle cx="6" cy="6" r="6" fill="#fff"/><rect x="2.8" y="3.8" width="6.4" height="4.4" fill="var(--green-mid)"/><path d="M2.8 3.8 6 6.4l3.2-2.6" stroke="#fff" stroke-width=".7" fill="none"/></svg>
      <span>info@vorantaimports.com</span>
    </li>
    <li>
      <svg viewBox="0 0 12 12"><circle cx="6" cy="6" r="6" fill="#fff"/><circle cx="6" cy="6" r="3.4" fill="none" stroke="var(--green-mid)" stroke-width=".9"/><path d="M2.6 6h6.8M6 2.6v6.8" stroke="var(--green-mid)" stroke-width=".8"/></svg>
      <span>www.vorantaimports.com</span>
    </li>
  </ul>
</section>

</body>
</html>
```